Bright Harbor Design

We need a web design for our startup company based in Zurich, Switzerland called Bright Harbor. We offer professional flirt and dating advice, self development with seminars and practical coachings.

The final website aims for two capital goals. First, it will contain text, pictures and video based content presenting and advertising our services. Furthermore, we want to bind our costumers with a plattform offering them to share their expiriences related with our services.

The targeted group will be men from 25 to 40 years.
Updates

The design requires also a register-box to put in the clients Name and Email

I need (besides of the "email registration box") a "Video Gallery", "Blog" and "Agenda (with the next events to come)"

Reason: I want to make a poll now

Target Market(s)

Guys around 25 to 40 years who want to improve their social lifestyle

Industry/Entity Type

Advertising

Requirements
Must have
• First and foremost, the design must transfer strong emotions and suggest an attractive social lifestyle.

The design should not be overloaded with content but should include pictures, videos and text.

The design should present a modern, urban lifestyle.
Nice to have
• There is a logo attached to the assignement. However, if you have a good idea for an improved or different logo, please do not hesitate to design your ideas.

```html
<!DOCTYPE html>
<html lang="en">
<head>
<meta charset="utf-8">
<title>Bright Harbor</title>
<link href="https://fonts.googleapis.com/css2?family=Questrial&family=Open+Sans:wght@400;600;700&display=swap" rel="stylesheet">
<style>
  :root {
    --bg-dark: #0b0503;
    --bg-deep: #1a0805;
    --amber: #b5581a;
    --rust: #8a2410;
    --white: #ffffff;
    --text-soft: #e8ddd8;
    --accent: #f7941d;
    --teal: #1f8a86;
    --olive: #a7a51c;
    --crimson: #a3182a;
    --btn-grey: #3a3533;
    --rule: #4a3430;
  }
  * { box-sizing: border-box; margin: 0; padding: 0; }
  html, body { width: 1175px; height: 1200px; overflow: hidden; background: var(--bg-dark); }
  .page { position: relative; width: 1175px; height: 1200px; overflow: hidden; color: var(--white);
    font-family: "Open Sans", Arial, sans-serif; }
  .backdrop { position: absolute; inset: 0; }
  .abs { position: absolute; }

  .auth-btn { top: 0; height: 38px; width: 80px; background: var(--white); color: #222;
    font-family: "Questrial", sans-serif; font-size: 12.5px; display: flex; align-items: center; justify-content: center; }
  .auth-btn.signup { left: 869px; }
  .auth-btn.signin { left: 957px; }

  .brand { left: 126px; top: 62px; display: flex; align-items: center; gap: 12px;
    font-family: "Questrial", sans-serif; font-size: 30px; color: var(--white); }
  .brand .dot { width: 30px; height: 30px; border-radius: 50%; background: var(--white); }

  .main-nav { right: 138px; top: 66px; display: flex; gap: 20px; font-family: "Questrial", sans-serif;
    font-size: 14.5px; letter-spacing: 2.4px; font-weight: 700; }

  .hero-photo { left: 520px; top: 95px; width: 537px; height: 362px;
    background: radial-gradient(ellipse at 60% 45%, #b98450 0%, #6b3a1c 45%, rgba(20,8,4,0) 75%); }

  .headline { left: 124px; top: 203px; width: 470px; font-family: "Questrial", sans-serif;
    font-size: 30px; line-height: 38px; font-weight: 400; text-transform: uppercase; letter-spacing: 0.3px; }
  .learn-btn { left: 124px; top: 335px; width: 150px; height: 38px; background: var(--white); color: #111;
    font-family: "Questrial", sans-serif; font-size: 13.5px; letter-spacing: 3px;
    display: flex; align-items: center; justify-content: center; }

  .tile { top: 456px; width: 300px; height: 186px; display: flex; flex-direction: column;
    align-items: center; justify-content: center; text-align: center; font-family: "Questrial", sans-serif; }
  .tile.guide { left: 122px; background: linear-gradient(135deg, #2a9490, #186d6a); }
  .tile.memories { left: 438px; background: linear-gradient(135deg, #b3ad26, #8c8a14); }
  .tile.videos { left: 753px; background: linear-gradient(135deg, #b22436, #86101f); }
  .tile .tile-text { font-size: 23px; line-height: 24px; }
  .tile .tile-title { font-size: 40px; line-height: 42px; }
  .tile .tile-sub { font-size: 15px; margin-top: 4px; }

  .section-title { font-family: "Questrial", sans-serif; font-size: 33px; font-weight: 400; top: 688px; }
  .section-sub { font-size: 13.5px; font-weight: 600; top: 726px; }
  .connections-title { left: 124px; }
  .connections-sub { left: 126px; }
  .register-title { left: 769px; }
  .register-sub { left: 770px; }

  .share-btn { left: 573px; top: 700px; width: 133px; height: 29px; background: var(--btn-grey);
    font-size: 10.5px; letter-spacing: 2px; font-weight: 600; display: flex; align-items: center; justify-content: center; }

  .story { left: 124px; width: 575px; font-size: 13.5px; line-height: 22.6px; color: var(--text-soft); }
  .story .more { color: var(--accent); font-weight: 700; font-size: 11.5px; text-transform: uppercase; margin-left: 4px; }
  .story.one { top: 768px; }
  .story.two { top: 887px; }
  .story.three { top: 988px; width: 560px; }

  .field-label { font-size: 14.5px; color: var(--text-soft); }
  .field { background: var(--white); height: 32px; border-radius: 2px; }
  .submit-btn { left: 915px; top: 1003px; width: 129px; height: 28px; background: var(--accent);
    font-size: 10.5px; letter-spacing: 2px; font-weight: 600; display: flex; align-items: center; justify-content: center; }

  .footer-rule { left: 125px; top: 1097px; width: 920px; height: 1px; background: var(--rule); }
  .footer-brand { left: 126px; top: 1124px; display: flex; align-items: center; gap: 8px;
    font-family: "Questrial", sans-serif; font-size: 17px; }
  .footer-brand .dot { width: 16px; height: 16px; border-radius: 50%; background: var(--white); }
  .footer-links { right: 131px; top: 1140px; font-size: 10.5px; font-weight: 600; }
</style>
</head>
<body>
<div class="page">
  <svg class="backdrop" width="1175" height="1200" viewBox="0 0 1175 1200" aria-hidden="true">
    <defs>
      <linearGradient id="glowTop" x1="0" y1="0" x2="1" y2="0.6">
        <stop offset="0" stop-color="#5a2a10"/>
        <stop offset="0.5" stop-color="#9a4816"/>
        <stop offset="1" stop-color="#2a1208"/>
      </linearGradient>
      <linearGradient id="band" x1="0" y1="1" x2="1" y2="0">
        <stop offset="0" stop-color="#7a1e0e"/>
        <stop offset="0.5" stop-color="#3d0f07"/>
        <stop offset="1" stop-color="#12060300"/>
      </linearGradient>
      <radialGradient id="lowGlow" cx="0.2" cy="0.8" r="0.6">
        <stop offset="0" stop-color="#6d1a0c"/>
        <stop offset="1" stop-color="#0b0503"/>
      </radialGradient>
    </defs>
    <rect width="1175" height="1200" fill="#0b0503"/>
    <rect y="640" width="1175" height="560" fill="url(#lowGlow)" opacity="0.8"/>
    <path d="M0 0 H1175 V140 C900 40 600 230 300 180 C150 160 50 210 0 200 Z" fill="url(#glowTop)"/>
    <path d="M0 840 L560 330 L1100 0 L1175 0 L1175 60 L620 420 L0 1000 Z" fill="url(#band)" opacity="0.9"/>
    <path d="M0 1000 L620 420 L1175 60 L1175 300 L700 600 L0 1200 Z" fill="#4a120a" opacity="0.35"/>
    <circle cx="1031" cy="62" r="4" fill="#fff" opacity="0.8"/>
    <circle cx="689" cy="136" r="4" fill="#fff" opacity="0.8"/>
    <circle cx="1090" cy="242" r="4" fill="#fff" opacity="0.6"/>
    <circle cx="16" cy="450" r="4" fill="#fff" opacity="0.6"/>
  </svg>

  <div class="hero-photo abs" role="img" aria-label="Photo of a young couple relaxing together in a warm-lit lounge"></div>

  <a class="auth-btn signup abs">SIGN UP</a>
  <a class="auth-btn signin abs">SIGN IN</a>

  <div class="brand abs"><span class="dot"></span><span>Bright Harbor</span></div>

  <nav class="main-nav abs">
    <span>HOW IT WORKS</span><span>CONNECTIONS</span><span>VIDEOS</span><span>CONTACT US</span>
  </nav>

  <h1 class="headline abs">Bright Harbor is exactly what you need to get your social life back on track</h1>
  <a class="learn-btn abs">LEARN MORE</a>

  <div class="tile guide abs" role="img" aria-label="Teal-toned photo of a couple talking on a city street">
    <div class="tile-text">How Can Bright<br>Harbor get you<br>back in the game</div>
  </div>
  <div class="tile memories abs" role="img" aria-label="Olive-toned photo of people meeting in a cafe">
    <div class="tile-text">Share some of<br>your bright harbor<br>memories with us</div>
  </div>
  <div class="tile videos abs" role="img" aria-label="Red-toned photo of a man at a pool table">
    <div class="tile-title">VIDEOS</div>
    <div class="tile-sub">Check out some of our videos</div>
  </div>

  <h2 class="section-title connections-title abs">Connections</h2>
  <p class="section-sub connections-sub abs">Past users Bright Harbor expereinces</p>
  <a class="share-btn abs">SHARE WITH US</a>

  <p class="story one abs">Lorem ipsum dolor sit amet, consectetur adipisicing elit, sed do eiusmod tempor incididunt ut labore et dolore magna aliqua. Ut enim ad minim veniam, quis nostrud exercitation ullamco laboris nisi ut aliquip ex ea commodo consequat. Duis aute irure dolor in reprehenderit in voluptate velit esse cillum dolore eu fugiat nulla pariatur. <span class="more">Read more</span></p>
  <p class="story two abs">Lorem ipsum dolor sit amet, consectetur adipisicing elit, sed do eiusmod tempor incididunt ut labore et dolore magna aliqua. Ut enim ad minim veniam, quis nostrud exercitation ullamco laboris nisi ut aliquip ex ea commodo consequat. Duis aute irure dolor henderit <span class="more">Read more</span></p>
  <p class="story three abs">Lorem ipsum dolor sit amet, consectetur adipisicing elit, sed do eiusmod tempor incididunt ut labore et dolore magna aliqua. Ut enim ad minim veniam, quis nostrud exercitation ullamco laboris nisi ut aliquip ex ea commodo consequat. <span class="more">Read more</span></p>

  <h2 class="section-title register-title abs">Register</h2>
  <p class="section-sub register-sub abs">It’s easy &amp; free to register, why not!</p>

  <span class="field-label abs" style="left:769px;top:771px;">Name</span>
  <div class="field abs" style="left:771px;top:795px;width:271px;"></div>
  <span class="field-label abs" style="left:769px;top:842px;">Email</span>
  <div class="field abs" style="left:771px;top:867px;width:271px;"></div>
  <span class="field-label abs" style="left:769px;top:913px;">Password</span>
  <span class="field-label abs" style="left:917px;top:913px;">Confirm</span>
  <div class="field abs" style="left:771px;top:938px;width:128px;"></div>
  <div class="field abs" style="left:915px;top:938px;width:128px;"></div>
  <a class="submit-btn abs">SIGN ME UP</a>

  <div class="footer-rule abs"></div>
  <div class="footer-brand abs"><span class="dot"></span><span>Bright Harbor</span></div>
  <div class="footer-links abs">© Bright Harbor | Privacy Policy | Terms of Use</div>
</div>
</body>
</html>
```